NZ First of it's kind solutions directory and marketplace for busy Mums needs a business card design

We need a business card design for our new nationwide business in NZ (long term plans to go global). We provide solutions to the everyday challenges that busy Mums face by connecting them with quality communities and suppliers of carefully selected, relevant products and services. We sell direct via our online marketplace. The final design should communicate our values of inclusivity, quality and smart solutions. Colours should incorporate our logo colour palette of #477077 and #6ba8b2. Our website is at https://www.brightnestmums.example

Target Market(s)

busy Mums, Age 28 – 50, female, income over $100K, location main centres NZ primarily but NZ wide. Is likely juggling work or career with a young family. Probably had hobbies which have fallen by the wayside.
-Wants to succeed in her chosen career without compromising on family life
-to successfully juggle her career without feeling like she is compromising her children
- Is time poor, something always has to give and it’s generally her health (she’ll stay up late, get stressed)
- probably ex corporate or professional career. Has discretional income

Industry/Entity Type

Business

Contact Information for Business Card

Lena Forbisher, Founder, BrightNestMums.example (Strapline Tap; Gather; Sorted), 47 Kowhai Terrace, Ellerslie, Auckland 1051, New Zealand. Mob: 021 483 517 Ph: +64 (0)9 571 4860

Font styles to use
Other font styles liked:
• Raleway, and/or Architects Daughter

Colors
00a990
33b8a4
86cfc6
cfeae6

Requirements
Must have
• the above details, streamline. the logo and colours associated with those logos
Should not have
• foil or metallic colours

```html
<!DOCTYPE html>
<html lang="en">
<head>
<meta charset="utf-8">
<title>Lena Forbisher – Business Card</title>
<link href="https://fonts.googleapis.com/css2?family=Rubik:wght@500&family=Roboto:ital,wght@0,400;1,400&display=swap" rel="stylesheet">
<style>
  :root {
    --page-bg: #d9d6d1;
    --card-bg: #eef0ef;
    --brand-deep: #477077;
    --brand-light: #6ba8b2;
    --ink: #2f3436;
    --ink-soft: #3c4548;
    --white: #ffffff;
  }
  html, body {
    margin: 0;
    width: 1200px;
    height: 1047px;
    overflow: hidden;
    background: var(--page-bg);
  }
  .business-card {
    position: absolute;
    left: 100px;
    top: 224px;
    width: 1000px;
    height: 598px;
    background: var(--card-bg);
    border-radius: 4px;
    overflow: hidden;
    box-shadow: 0 10px 30px rgba(0,0,0,0.15);
  }
  .brand-panel {
    position: absolute;
    inset: 0;
  }
  .brand-name {
    position: absolute;
    left: 0;
    width: 450px;
    top: 272px;
    text-align: center;
    font-family: "Rubik", sans-serif;
    font-weight: 500;
    font-size: 34px;
    color: var(--white);
    margin: 0;
  }
  .brand-mark {
    position: absolute;
    left: 195px;
    top: 190px;
    width: 60px;
    height: 60px;
    border-radius: 50%;
    background: var(--white);
  }
  .identity {
    position: absolute;
    right: 52px;
    top: 56px;
    text-align: right;
  }
  .person-name {
    margin: 0;
    font-family: "Rubik", sans-serif;
    font-weight: 500;
    font-size: 40px;
    color: var(--ink);
    letter-spacing: 0.2px;
  }
  .person-role {
    margin: 2px 0 0;
    font-family: "Roboto", sans-serif;
    font-style: italic;
    font-size: 23px;
    color: var(--ink-soft);
  }
  .address {
    position: absolute;
    right: 52px;
    top: 320px;
    margin: 0;
    text-align: right;
    font-family: "Roboto", sans-serif;
    font-style: normal;
    font-size: 23px;
    line-height: 38px;
    color: var(--ink);
  }
  .contact-list {
    position: absolute;
    right: 52px;
    top: 412px;
    margin: 0;
    padding: 0;
    list-style: none;
    font-family: "Roboto", sans-serif;
    font-size: 23px;
    line-height: 37px;
    color: var(--ink);
  }
  .contact-item {
    display: flex;
    justify-content: flex-end;
    align-items: center;
    gap: 12px;
  }
  .contact-icon {
    width: 20px;
    height: 20px;
    fill: var(--ink-soft);
  }
</style>
</head>
<body>
  <main class="business-card">
    <svg class="brand-panel" width="1000" height="598" viewBox="0 0 1000 598" aria-hidden="true">
      <path d="M0 0 H448 Q580 299 442 598 H0 Z" fill="var(--brand-light)" opacity="0.55"/>
      <path d="M0 0 H425 Q555 299 420 598 H0 Z" fill="var(--brand-deep)"/>
    </svg>
    <span class="brand-mark" aria-hidden="true"></span>
    <p class="brand-name">BrightNestMums</p>

    <header class="identity">
      <h1 class="person-name">Lena Forbisher</h1>
      <p class="person-role">Founder</p>
    </header>

    <address class="address">
      47 Kowhai Terrace, Ellerslie,<br>
      Auckland 1051, New Zealand
    </address>

    <ul class="contact-list">
      <li class="contact-item">021 483 517
        <svg class="contact-icon" viewBox="0 0 20 20" aria-hidden="true"><rect x="5" y="1" width="10" height="18" rx="2"/><rect x="7" y="4" width="6" height="9" fill="var(--card-bg)"/></svg>
      </li>
      <li class="contact-item">+64 (0)9 571 4860
        <svg class="contact-icon" viewBox="0 0 20 20" aria-hidden="true"><path d="M2 6 Q10 1 18 6 L16 9 L13 7 L7 7 L4 9 Z"/><rect x="4" y="10" width="12" height="8" rx="1"/></svg>
      </li>
      <li class="contact-item">www.BrightNestMums.example
        <svg class="contact-icon" viewBox="0 0 20 20" aria-hidden="true"><rect x="1" y="4" width="18" height="12"/><path d="M1 4 L10 11 L19 4" fill="none" stroke="var(--card-bg)" stroke-width="1.6"/></svg>
      </li>
      <li class="contact-item">lenaforbisher@brightnestmums.example
        <svg class="contact-icon" viewBox="0 0 20 20" aria-hidden="true"><circle cx="10" cy="10" r="9"/><path d="M1 10 H19 M10 1 Q4 10 10 19 M10 1 Q16 10 10 19" fill="none" stroke="var(--card-bg)" stroke-width="1.3"/></svg>
      </li>
    </ul>
  </main>
</body>
</html>
```